Gift Cards in the Mail Envelope

Mailing out gift cards in the envelope. Need an eye popping envelope. Please look at the enclosed images. The envelope should look like that.

Low design quality

```html
<!DOCTYPE html>
<html lang="en">
<head>
<meta charset="utf-8">
<title>Gift Card Mailing Envelope</title>
<style>
  :root {
    --backdrop: #d9d9d9;
    --paper-deep: #640000;
    --paper-mid: #8a4a08;
    --paper-bright: #b3a30f;
    --flap-deep: #650a05;
    --flap-bright: #8a3c0a;
    --window: #fec4c4;
    --shadow: rgba(0, 0, 0, 0.35);
  }
  html, body {
    margin: 0;
    padding: 0;
    overflow: hidden;
  }
  body {
    width: 1200px;
    height: 1200px;
    background: var(--backdrop);
    position: relative;
  }
  .envelope {
    position: absolute;
    box-shadow: 0 2px 4px var(--shadow);
  }
  .envelope__pattern {
    position: absolute;
    inset: 0;
    background: linear-gradient(205deg, var(--paper-bright) 0%, var(--paper-bright) 18%, var(--paper-mid) 50%, var(--paper-deep) 82%, var(--paper-deep) 100%);
  }
  .envelope--front {
    left: 190px;
    top: 192px;
    width: 818px;
    height: 410px;
  }
  .envelope__window {
    position: absolute;
    left: 73px;
    top: 58px;
    width: 343px;
    height: 158px;
    background: var(--window);
  }
  .envelope--back {
    left: 193px;
    top: 704px;
    width: 813px;
    height: 404px;
  }
  .envelope__flap {
    position: absolute;
    left: 0;
    top: 0;
    width: 813px;
    height: 220px;
  }
</style>
</head>
<body>
  <div class="envelope envelope--front">
    <div class="envelope__pattern" role="img" aria-label="Polka dot pattern on a red to golden olive gradient"></div>
    <div class="envelope__window"></div>
  </div>

  <div class="envelope envelope--back">
    <div class="envelope__pattern" role="img" aria-label="Polka dot pattern on a red to golden olive gradient"></div>
    <svg class="envelope__flap" viewBox="0 0 813 220" aria-hidden="true">
      <defs>
        <linearGradient id="flapShade" x1="0" y1="1" x2="1" y2="0">
          <stop offset="0" stop-color="var(--flap-deep)"/>
          <stop offset="0.45" stop-color="var(--flap-deep)"/>
          <stop offset="1" stop-color="var(--flap-bright)"/>
        </linearGradient>
      </defs>
      <path d="M6 0 H807 V38 Q807 54 790 62 L416 207 Q406 211 396 207 L24 62 Q6 54 6 38 Z" fill="url(#flapShade)"/>
    </svg>
  </div>
</body>
</html>
```